Business Card Design Project

I have a need for a business card designed. I have a logo.. but need looking for a nice card to go with it. The school is called The Institute of Combat Studies is the name of the school. Some ideas for what I want on the card.
Guru Rob Tessler
over 25 years martial arts experience
Private and group lessons
kids and adult classes
No contracts or testing fees
styles we teach are escrima, silat, kenpo, and MMA
website is www.ridgelinedojo.example
phone is 555-214-7730
visit us on face book at https://www.socialpage.example/pages/The-Institute-of-Combat-Studies/804392615570218

Target Market(s)

adults 1st kids second.

Industry/Entity Type

School

Requirements
Must have
• Guru Rob Tessler
Private and group lessons
phone is 555-214-7730

```html
<!DOCTYPE html>
<html lang="en">
<head>
<meta charset="utf-8">
<title>The Institute of Combat Studies – Business Card</title>
<link href="https://fonts.googleapis.com/css2?family=Open+Sans:ital,wght@0,400;0,600;0,700;0,800;1,600&family=Roboto+Condensed:ital,wght@1,300&display=swap" rel="stylesheet">
<style>
  :root {
    --sky: #cdf5fb;
    --paper: #ffffff;
    --card-black: #050505;
    --frame-yellow: #f4e81c;
    --band-yellow: #fbf21a;
    --band-red: #b40e0a;
    --ink-white: #ffffff;
    --ink-black: #111111;
    --label-ink: #222222;
  }
  * { margin: 0; padding: 0; box-sizing: border-box; }
  html, body { width: 1200px; height: 780px; overflow: hidden; }
  body {
    position: relative;
    background: linear-gradient(to bottom, var(--sky) 0%, #e6fafd 55%, var(--paper) 100%);
    font-family: "Open Sans", Arial, sans-serif;
  }
  .card {
    position: absolute;
    background: var(--card-black);
    box-shadow: 0 12px 14px -8px rgba(0,0,0,0.35);
  }
  .card__frame {
    position: absolute;
    inset: 13px 14px 14px 14px;
    border: 2px solid var(--frame-yellow);
  }
  .card--front { left: 30px; top: 318px; width: 682px; height: 388px; }
  .card--back  { left: 757px; top: 25px; width: 389px; height: 681px; }

  .school-name {
    position: absolute;
    display: flex;
    flex-direction: column;
    align-items: center;
    justify-content: center;
    gap: 16px;
    color: var(--band-yellow);
    font-weight: 800;
    text-transform: uppercase;
    text-align: center;
    line-height: 1.1;
    font-size: 36px;
  }
  .school-name__dot {
    flex: none;
    width: 74px;
    height: 74px;
    border-radius: 50%;
    background: var(--band-yellow);
  }
  .card--front .school-name { left: 166px; top: 46px; width: 350px; height: 290px; }
  .card--back .school-name { left: 20px; top: 38px; width: 349px; height: 290px; }

  .styles {
    position: absolute;
    left: 14px; right: 14px; top: 340px;
    color: var(--ink-white);
    font-weight: 800;
    font-size: 38px;
    line-height: 45px;
    text-align: center;
    letter-spacing: 0.5px;
  }
  .styles__small { font-size: 29px; }

  .instructor {
    position: absolute;
    left: 14px; right: 14px; top: 441px; height: 67px;
    background: var(--band-yellow);
    color: var(--ink-black);
    text-align: center;
  }
  .instructor__name { font-weight: 700; font-size: 25px; line-height: 30px; margin-top: 8px; }
  .instructor__note { font-style: italic; font-weight: 600; font-size: 15.5px; line-height: 20px; }

  .perks {
    position: absolute;
    left: 14px; right: 14px; top: 527px;
    list-style: none;
    color: var(--ink-white);
    font-size: 19.5px;
    line-height: 26px;
    text-align: center;
  }

  .contact {
    position: absolute;
    left: 14px; right: 14px; top: 596px; height: 69px;
    background: var(--band-red);
    color: var(--ink-white);
    text-align: center;
    font-weight: 800;
  }
  .contact__phone { font-size: 30px; line-height: 36px; margin-top: 3px; letter-spacing: 0.5px; }
  .contact__web { font-size: 16px; line-height: 22px; letter-spacing: 0.6px; }

  .side-label {
    position: absolute;
    top: 722px;
    font-family: "Roboto Condensed", Arial, sans-serif;
    font-style: italic;
    font-weight: 300;
    font-size: 31px;
    color: var(--label-ink);
    text-align: center;
    width: 200px;
  }
  .side-label--front { left: 271px; }
  .side-label--back { left: 851px; }
</style>
</head>
<body>
  <section class="card card--front" aria-label="Card front">
    <div class="card__frame"></div>
    <div class="school-name"><span class="school-name__dot"></span><span>The Institute<br>of Combat<br>Studies</span></div>
  </section>

  <section class="card card--back" aria-label="Card back">
    <div class="card__frame"></div>
    <div class="school-name"><span class="school-name__dot"></span><span>The Institute<br>of Combat<br>Studies</span></div>
    <h2 class="styles">ESCRIMA, SILAT,<br>KENPO <span class="styles__small">AND</span> MMA</h2>
    <div class="instructor">
      <p class="instructor__name">Guru Rob Tessler</p>
      <p class="instructor__note">over 25 years martial arts experience</p>
    </div>
    <ul class="perks">
      <li>• Private and group lessons</li>
      <li>• No contracts or testing fees</li>
    </ul>
    <div class="contact">
      <p class="contact__phone">555-214-7730</p>
      <p class="contact__web">www.ridgelinedojo.example</p>
    </div>
  </section>

  <p class="side-label side-label--front">FRONT</p>
  <p class="side-label side-label--back">BACK</p>
</body>
</html>
```